Silver Meadow LLC business card

I help with the Marketing and Sales of various Natural, Organic, Eco Friendly and Healthy Main Stream products to Retail Corporate accounts as well as Independents and Distributors.I also highlight Private label items to these same Retail Corporate accounts.Cherish the Moments, Enjoy Life!

Speciality & Health Sales and Marketing

Target Market(s)

Men and Women

Industry/Entity Type

Business

Contact Information for Business Card

Silver Meadow, LLC
Janet Louise Verhagen
438 West Finch Lane
Ste 4-237
Phoenix, AZ 85047
602-555-0147
jverhagen@plumvale.net

Requirements
Must have
• Nice, femine font
Something in the background or on a side with a softness
Nice to have
• Cherish the Moments, Enjoy Life
Should not have
• Hardness

```html
<!DOCTYPE html>
<html lang="en">
<head>
<meta charset="utf-8">
<title>Silver Meadow LLC – Business Card</title>
<link href="https://fonts.googleapis.com/css2?family=Lato:wght@400;700&display=swap" rel="stylesheet">
<style>
  :root {
    --orange: #e96a28;
    --ink: #3a3a3a;
    --muted: #6b6b6b;
    --paper: #ffffff;
    --backdrop: #eeeeee;
  }
  * { box-sizing: border-box; margin: 0; padding: 0; }
  html, body {
    width: 1200px;
    height: 900px;
    overflow: hidden;
    background: var(--backdrop);
    font-family: "Lato", Arial, sans-serif;
  }
  .canvas {
    position: relative;
    width: 1200px;
    height: 900px;
  }
  .card {
    position: absolute;
    top: 313px;
    width: 480px;
    height: 274px;
    box-shadow: 0 6px 18px rgba(0,0,0,0.12);
  }
  .card--front {
    left: 90px;
    background: var(--paper);
    padding: 30px 32px;
  }
  .card--back {
    left: 630px;
    background: var(--orange);
    display: flex;
    align-items: center;
    justify-content: center;
    gap: 14px;
  }
  .holder-name {
    font-size: 21px;
    font-weight: 700;
    color: var(--orange);
    line-height: 1.1;
  }
  .holder-title {
    font-size: 11px;
    color: var(--muted);
    margin-top: 3px;
  }
  .contact-list {
    list-style: none;
    margin-top: 26px;
  }
  .contact-item { margin-bottom: 4px; }
  .contact-label {
    display: block;
    font-size: 11px;
    color: var(--orange);
    line-height: 1.15;
  }
  .contact-value {
    display: block;
    font-size: 12px;
    color: var(--ink);
    line-height: 1.2;
  }
  .brand {
    position: absolute;
    right: 30px;
    bottom: 34px;
    display: flex;
    align-items: center;
    gap: 8px;
  }
  .brand-dot {
    width: 30px;
    height: 30px;
    border-radius: 50%;
    background: var(--orange);
  }
  .brand-name {
    font-size: 16px;
    font-weight: 700;
    letter-spacing: 0.5px;
    text-transform: uppercase;
    color: var(--ink);
  }
  .back-dot {
    width: 56px;
    height: 56px;
    border-radius: 50%;
    background: var(--paper);
  }
  .back-name {
    font-size: 26px;
    font-weight: 700;
    letter-spacing: 1px;
    text-transform: uppercase;
    color: var(--paper);
  }
</style>
</head>
<body>
<main class="canvas">
  <section class="card card--front" aria-label="Business card front">
    <h1 class="holder-name">Janet Louise Verhagen</h1>
    <p class="holder-title">Managing Director</p>
    <ul class="contact-list">
      <li class="contact-item">
        <span class="contact-label">telephone</span>
        <span class="contact-value">602-555-0147</span>
      </li>
      <li class="contact-item">
        <span class="contact-label">email</span>
        <span class="contact-value">jverhagen@plumvale.net</span>
      </li>
      <li class="contact-item">
        <span class="contact-label">address</span>
        <span class="contact-value">438 West Finch Lane, Ste 4-237, Phoenix, AZ 85047</span>
      </li>
    </ul>
    <div class="brand">
      <span class="brand-dot" aria-hidden="true"></span>
      <span class="brand-name">Silver Meadow LLC</span>
    </div>
  </section>

  <section class="card card--back" aria-label="Business card back">
    <span class="back-dot" aria-hidden="true"></span>
    <span class="back-name">Silver Meadow LLC</span>
  </section>
</main>
</body>
</html>
```